KTWG application splash screen

We need a 1024x768 image for use as an application splash screen.
The image will be displayed full screen on an 10 inch industrial PC 1024x768 screen while our application is launching. The image should convey that the application is "Waiting for connection to Wi-Fi access point..." and include a graphic of the industrial PC connected to the access point via an Ethernet cable. A list of troubleshooting steps should be included at the bottom of the image. The troubleshooting steps should not be the main focus of the image and should be shown in a smaller font (but still readable at 1024x768 displayed on a 10 inch screen).
I will include a mock up of the general idea of what we are looking for as well as image files for the industrial PC, a screenshot of our application to show on the PC's screen and the AP.
For general look and feel and a sense of corporate branding please review our website https://marrowgatesoilworks.example/. The splash screen should reflect corporate branding.
Target Market(s)
Users of our application
Industry/Entity Type
Agriculture
Look and feel

```html
<!DOCTYPE html>
<html lang="en">
<head>
<meta charset="utf-8">
<title>KTWG – Waiting for Wi-Fi access point</title>
<link rel="stylesheet" href="https://fonts.googleapis.com/css2?family=Lexend:wght@400;500;600&display=swap">
<style>
  :root {
    --field-green: #40bb64;
    --panel-green: #24994a;
    --ink-white: #ffffff;
    --cable-black: #111111;
    --device-dark: #2a2a2a;
    --ap-light: #f2f2f2;
    --ap-shade: #d9d9d9;
  }
  html, body {
    margin: 0;
    padding: 0;
    overflow: hidden;
    background: var(--field-green);
  }
  .splash {
    position: relative;
    width: 1200px;
    height: 900px;
    overflow: hidden;
    background: var(--field-green);
    color: var(--ink-white);
    font-family: "Lexend", sans-serif;
  }
  .brand {
    position: absolute;
    left: 40px;
    top: 50px;
    display: flex;
    align-items: center;
    gap: 12px;
    font-size: 58px;
    font-weight: 600;
    letter-spacing: 2px;
    line-height: 1;
  }
  .brand-mark {
    width: 18px;
    height: 18px;
    border-radius: 50%;
    background: var(--ink-white);
  }
  .headline {
    position: absolute;
    left: 200px;
    top: 30px;
    width: 815px;
    margin: 0;
    text-align: center;
    font-size: 74px;
    font-weight: 600;
    line-height: 80px;
  }
  .diagram {
    position: absolute;
    left: 0;
    top: 0;
  }
  .label {
    position: absolute;
    text-align: center;
    font-weight: 500;
    line-height: 1.05;
  }
  .label-computer {
    left: 52px;
    top: 518px;
    width: 260px;
    font-size: 31px;
  }
  .label-cable {
    left: 496px;
    top: 426px;
    width: 290px;
    font-size: 30px;
  }
  .label-ap {
    left: 830px;
    top: 516px;
    width: 340px;
    font-size: 31px;
  }
  .label-ap small {
    display: block;
    margin-top: 4px;
    font-size: 20px;
    font-weight: 500;
  }
  .troubleshooting {
    position: absolute;
    left: 33px;
    top: 607px;
    width: 1137px;
    height: 258px;
    box-sizing: border-box;
    border: 3px solid var(--ink-white);
    background: var(--panel-green);
    padding: 10px 20px 0 20px;
  }
  .troubleshooting h2 {
    margin: 0 0 6px 0;
    font-size: 31px;
    font-weight: 500;
    line-height: 36px;
  }
  .steps, .steps ul {
    margin: 0;
    padding: 0;
    list-style: none;
  }
  .steps li {
    font-size: 20.5px;
    line-height: 23.5px;
    font-weight: 500;
    padding-left: 14px;
    text-indent: -14px;
  }
  .steps li::before { content: "• "; }
  .steps ul { padding-left: 30px; }
  .steps ul li { padding-left: 20px; text-indent: -20px; }
  .steps ul li::before { content: "→ "; }
</style>
</head>
<body>
<main class="splash">
  <div class="brand" aria-label="KTWG">
    <span class="brand-mark"></span>
    <span>KTWG</span>
  </div>

  <h1 class="headline">Waiting for connection to Wi-Fi access point...</h1>

  <svg class="diagram" width="1200" height="900" viewBox="0 0 1200 900">
    <defs>
      <linearGradient id="ap-fill" x1="0" y1="0" x2="1" y2="0">
        <stop offset="0" stop-color="var(--ap-light)"/>
        <stop offset="1" stop-color="var(--ap-shade)"/>
      </linearGradient>
    </defs>
    <path class="ethernet-cable" d="M320 478 H1111 V462" fill="none" stroke="var(--cable-black)" stroke-width="5"/>
    <rect class="cab-computer" role="img" aria-label="Photo of the tractor cab computer showing the seeding application screen"
          x="23" y="279" width="299" height="237" rx="12" fill="var(--device-dark)"/>
    <rect class="access-point" role="img" aria-label="Photo of the outdoor Wi-Fi access point"
          x="1091" y="258" width="40" height="205" rx="8" fill="url(#ap-fill)"/>
  </svg>

  <div class="label label-computer">Tractor cab<br>computer</div>
  <div class="label label-cable">Ethernet cable</div>
  <div class="label label-ap">Wi-Fi Access Point<small>Norvane AX-220 Outdoor</small></div>

  <section class="troubleshooting">
    <h2>Troubleshooting steps:</h2>
    <ul class="steps">
      <li>This screen should only be visible for a short time on boot.</li>
      <li>If this screen stays visible for more than a minute:
        <ul>
          <li>Verify that the Wi-Fi Access Point (AP) powers up when this system does (indicated by a green light on the side of the AP).</li>
          <li>Check the Ethernet cable between this system and the AP for damage, and replace it if necessary.</li>
          <li>Power-cycle this system and wait for it to reboot fully.</li>
          <li>If the issue persists, contact KTWG support for further assistance.</li>
        </ul>
      </li>
    </ul>
  </section>
</main>
</body>
</html>
```